Building company buisness cards

We are looking for a sharp modern new look for our business cards.
We are a New Zealand based company that specialises in house and land packages.
We have attached a photo of the current logo and would like to see if it can be improved somehow if needed.
We are open to any colours but we have chosen green at this stage.
Feel free to change the font and make the logo smarter looking.
Play with the colours and see what looks best.

We want a card that looks so good know one will want to throw it away!

Target Market(s)

Home buyers

Industry/Entity Type

Building

Contact Information for Business Card

Derek Tolvane
0217394062
dtolvane@quillmarkhomesteads.co.nz
quillmarkhomesteads.co.nz

Font styles to use
Serif
Sans Serif

Colors

Designer to choose colors to be used in the design.

Requirements
Must have
• Logo and company name on one side, details on the other side
Nice to have
• Color codes for the original green are HEX #4a8028, RGB(74,128,40), CMYK(42,0,69,50)
• Round corners, Raised and/or spot UV

```html
<!DOCTYPE html>
<html lang="en">
<head>
<meta charset="utf-8">
<title>Quillmark Homesteads — Business Card</title>
<link rel="stylesheet" href="https://fonts.googleapis.com/css2?family=Ubuntu:wght@400;700&display=swap">
<style>
  :root {
    --green: #4e7a3f;
    --green-dark: #3f6a31;
    --green-light: #5f8f4d;
    --white: #ffffff;
    --off-white: #f2f2f2;
    --grey-band: #a9a6aa;
    --page: #e9e7e4;
  }
  * { box-sizing: border-box; margin: 0; padding: 0; }
  html, body { width: 1200px; height: 1021px; overflow: hidden; }
  body {
    background: var(--page);
    font-family: "Ubuntu", sans-serif;
    display: flex;
    flex-direction: column;
    align-items: center;
    justify-content: center;
    gap: 56px;
  }
  .card {
    position: relative;
    width: 770px;
    height: 440px;
    border-radius: 32px;
    overflow: hidden;
    box-shadow: 0 6px 18px rgba(0,0,0,0.18);
  }

  /* Back side */
  .card-back { background: var(--green); }
  .card-back .pattern-area {
    position: absolute; inset: 0;
    background: linear-gradient(120deg, var(--green-light) 0%, var(--green) 50%, var(--green-dark) 100%);
  }
  .card-back .brand {
    position: absolute; inset: 0;
    display: flex; align-items: center; justify-content: center; gap: 14px;
    color: var(--white);
  }
  .brand-mark {
    width: 22px; height: 22px; border-radius: 50%;
    background: currentColor; flex: none;
  }
  .brand-name {
    font-weight: 700;
    font-size: 44px;
    letter-spacing: 0.5px;
    line-height: 1;
    white-space: nowrap;
  }

  /* Front side */
  .card-front { background: var(--green); }
  .card-front .shape { position: absolute; inset: 0; }
  .card-front .brand {
    position: absolute; left: 170px; top: 96px;
    display: flex; align-items: center; gap: 14px;
    color: var(--green);
  }
  .card-front .brand-name { font-size: 44px; }
  .person {
    position: absolute; left: 64px; top: 262px;
    color: var(--white);
  }
  .person-name { font-weight: 700; font-size: 26px; }
  .person-role { font-size: 17px; margin-top: 2px; }
  .contact {
    position: absolute; right: 50px; bottom: 40px;
    list-style: none;
    color: var(--white);
    font-size: 18px;
    text-align: right;
    line-height: 1.55;
  }
  .contact li { display: flex; align-items: center; justify-content: flex-end; gap: 10px; white-space: nowrap; }
  .contact svg { width: 17px; height: 17px; flex: none; }
</style>
</head>
<body>

  <section class="card card-back" aria-label="Card back">
    <div class="pattern-area" role="img" aria-label="Raised spot UV repeating pattern of the house emblem"></div>
    <div class="brand">
      <span class="brand-mark"></span>
      <span class="brand-name">quillmark homesteads.</span>
    </div>
  </section>

  <section class="card card-front" aria-label="Card front">
    <svg class="shape" viewBox="0 0 770 440" preserveAspectRatio="none" aria-hidden="true">
      <path d="M0 0 H770 V292 C560 292 260 250 90 180 C50 164 20 152 0 144 Z" fill="var(--grey-band)"/>
      <path d="M0 0 H770 V272 C560 274 260 232 90 166 C50 150 20 140 0 132 Z" fill="var(--off-white)"/>
    </svg>
    <div class="brand">
      <span class="brand-mark"></span>
      <span class="brand-name">quillmark homesteads.</span>
    </div>
    <div class="person">
      <p class="person-name">Derek Tolvane</p>
      <p class="person-role">Founder</p>
    </div>
    <ul class="contact">
      <li>0217394062
        <svg viewBox="0 0 24 24" aria-hidden="true"><path fill="#fff" d="M6.6 10.8a15 15 0 0 0 6.6 6.6l2.2-2.2a1 1 0 0 1 1-.25 11.4 11.4 0 0 0 3.6.57 1 1 0 0 1 1 1V20a1 1 0 0 1-1 1A17 17 0 0 1 3 4a1 1 0 0 1 1-1h3.5a1 1 0 0 1 1 1c0 1.25.2 2.45.57 3.57a1 1 0 0 1-.25 1z"/></svg>
      </li>
      <li>dtolvane@quillmarkhomesteads.co.nz
        <svg viewBox="0 0 24 24" aria-hidden="true"><rect x="2.5" y="5" width="19" height="14" fill="none" stroke="#fff" stroke-width="2"/><path d="M2.5 5l9.5 8 9.5-8" fill="none" stroke="#fff" stroke-width="2"/></svg>
      </li>
      <li>quillmarkhomesteads.co.nz
        <svg viewBox="0 0 24 24" aria-hidden="true"><g fill="none" stroke="#fff" stroke-width="1.8"><circle cx="12" cy="12" r="9.5"/><ellipse cx="12" cy="12" rx="4.2" ry="9.5"/><path d="M2.5 12h19M4 7h16M4 17h16"/></g></svg>
      </li>
    </ul>
  </section>

</body>
</html>
```